Logo & Visitenkarte für Weinbauer
Zielgruppe
Ich bin Weinbauer und betreibe auch einen Buschenschank. Zielgruppe ist die Gastronomie und der (Durchschnitts-) Endverbraucher.
Aufgabenstellung
Unsere Betriebsstätte ist im Rebhügelgau Weinviertel (Österreich).
Wir wollen die Werte Tradition, Regional, Vertrauen und Bodenständigkeit vermitteln.
Unsere Kunden schätzen die Herkunft.
Das Logo soll als Firmenlogo und auch für die Weinetiketten verwendet werden können.

```html
<!DOCTYPE html>
<html lang="de">
<head>
<meta charset="utf-8">
<title>Weingut Hollerer – Visitenkarte</title>
<link rel="stylesheet" href="https://fonts.googleapis.com/css2?family=Oswald:wght@300&display=swap">
<style>
  :root {
    --bg: #dbe9ef;
    --paper: #f7f7f7;
    --wine: #8e1a22;
    --wine-ink: #8e1a22;
    --on-wine: #f1dede;
  }
  * { box-sizing: border-box; margin: 0; padding: 0; }
  html, body { width: 1200px; height: 900px; overflow: hidden; }
  body {
    background: var(--bg);
    display: flex;
    align-items: center;
    justify-content: center;
    gap: 60px;
    font-family: "Oswald", "Arial Narrow", sans-serif;
    font-weight: 300;
  }
  .card {
    width: 460px;
    height: 300px;
    display: flex;
    align-items: center;
    justify-content: center;
    box-shadow: 0 18px 40px rgba(60, 90, 105, 0.25);
  }
  .card--front { background: var(--paper); }
  .card--back { background: var(--wine); }
  .brand {
    display: flex;
    align-items: center;
    gap: 14px;
    color: var(--wine-ink);
  }
  .brand__dot {
    width: 18px;
    height: 18px;
    border-radius: 50%;
    background: var(--wine-ink);
  }
  .brand__name {
    font-size: 30px;
    letter-spacing: 0.12em;
    text-transform: uppercase;
    line-height: 1;
  }
  .address {
    list-style: none;
    color: var(--on-wine);
    font-size: 19px;
    letter-spacing: 0.12em;
    line-height: 1.45;
    text-transform: uppercase;
    text-align: left;
  }
</style>
</head>
<body>
  <section class="card card--front" aria-label="Vorderseite">
    <div class="brand">
      <span class="brand__dot"></span>
      <span class="brand__name">Weingut Hollerer</span>
    </div>
  </section>
  <section class="card card--back" aria-label="Rückseite">
    <ul class="address">
      <li>Musterweg 1</li>
      <li>Rebhügelgau</li>
      <li>Österreich</li>
    </ul>
  </section>
</body>
</html>
```